Website for Reiki and Wellness Courses

I teach online courses in Reiki and wellness/self-development and am needing a new website.

The focus of the website will be to provide descriptions of the courses as well as include a blog and pages where students in my courses will visit for additional information.

Note: courses are NOT hosted on this site.
The focus of this website will be to encourage viewers to enroll in courses as well as opt in to the email list.

I will upload copy soon. My old website is: http://brightfernstudies.example. Please do not use existing logo.

Target Market(s)

Alternative health, wellness, spirituality, personal development. Males and females of all ages seeking to improve their health and life.

Industry/Entity Type

Health And Wellness

Logo Text

No text (please do not use existing logo)

Coding

Coded - Design and coding required

Number of Pages Required

5+ page

Requirements
Must have
• 1. Home page
• 2. About page
• 3. Courses page that outlines courses (there are currently 6 courses with 1 coming soon)
• 4. Individual course page (maybe a template that I can adjust color and pictures for with each course)
• 5. Blog
• 6. Student Area that outlines all Student Areas
• 7. Individual Student Area page (maybe a template that I can adjust color and pictures for with each course)
• 8. Shop page (note: items will not currently be purchased through website - it will be a link to quillmarket for a book).
• 9. Student thank-you page (maybe a template that I can adjust color and pictures for with each course) this is the page students are directed to at end of course with vouchers for other courses.
• Opt-in for the home page, course pages, blog and thank-you pages
Nice to have
• I would like the design to be calm, clean and soothing. Ideally visitors feel relaxed when viewing the site and are encouraged to explore the courses, subscribe to the email list and purchase a product.
• ~ Testimonials page
• ~ Contact page
• I tend to gravitate towards blues, greys and purples as well as monochromatic color schemes.
Should not have
• Contact form on home page
• phone number on home page
• location/physical address
• dates for blog posts

```html
<!DOCTYPE html>
<html lang="en">
<head>
<meta charset="utf-8">
<title>Bright Fern Studies — Reiki &amp; Wellness Courses</title>
<link rel="stylesheet" href="https://fonts.googleapis.com/css2?family=Montserrat:wght@400;500;600&family=Open+Sans:ital,wght@0,400;0,600;1,400&display=swap">
<style>
:root{
  --slate:#6d7199;
  --slate-dark:#4f5480;
  --ink:#333333;
  --muted:#8a8a8a;
  --gold:#e9a714;
  --gold-light:#f4bf2a;
  --quote:#3c6db0;
  --light:#f2f2f2;
  --footer:#333333;
  --footer-bar:#4b4b4b;
  --white:#ffffff;
}
*{margin:0;padding:0;box-sizing:border-box}
html,body{width:1200px;height:2332px;overflow:hidden}
body{position:relative;background:var(--white);font-family:"Open Sans",Arial,sans-serif;color:var(--ink)}

/* Header */
.site-header{position:absolute;left:0;top:0;width:1200px;height:96px;background:var(--white)}
.brand{position:absolute;left:137px;top:28px;display:flex;align-items:center;gap:10px;font-family:"Montserrat",sans-serif;font-size:19px;font-weight:500;color:var(--slate)}
.brand-mark{width:30px;height:30px;background:var(--slate);border-radius:50%}
.main-nav a{position:absolute;top:53px;font-family:"Open Sans",sans-serif;font-size:16px;color:#444;text-decoration:none}
.main-nav a.active{color:var(--slate)}
.nav-marker{position:absolute;left:503px;top:18px;width:22px;height:22px;background:var(--slate);transform:rotate(45deg)}

/* Hero */
.hero{position:absolute;left:0;top:96px;width:1200px;height:480px;overflow:hidden}
.hero-photo{position:absolute;inset:0;background:linear-gradient(100deg,#8a7a66 0%,#c9b9a6 14%,#e8ded4 26%,#b9c8dc 45%,#8ea8c9 70%,#5f87b8 100%)}
.hero-sea{position:absolute;left:0;right:0;top:300px;height:180px;background:linear-gradient(180deg,#4f86c0,#2f6aa8)}
.hero-title{position:absolute;left:143px;top:190px;font-family:"Montserrat",sans-serif;color:var(--white);line-height:1.05}
.hero-title .line1{display:block;font-size:47px;font-weight:500}
.hero-title .line2{display:block;font-size:36px;font-weight:500}
.hero-wave{position:absolute;left:0;bottom:0;width:1200px;height:70px}
.slider-dots{position:absolute;display:flex;gap:8px}
.slider-dots span{width:18px;height:18px;border-radius:50%;background:var(--white)}
.slider-dots span.current{background:transparent;border:2px solid var(--white)}
.dots-grey span{background:#a9a9a9}
.dots-grey span.current{border-color:#a9a9a9;background:transparent}

.optin{position:absolute;left:777px;top:104px;width:297px;height:266px;background:rgba(236,238,242,.93);padding:28px 25px 0}
.optin h2{font-family:"Open Sans",sans-serif;font-weight:400;font-size:22px;color:#222;margin-bottom:12px}
.optin .field{height:33px;background:var(--white);border:1px solid #cfcfd4;margin-bottom:9px;font-size:12px;color:#888;padding:8px 11px}
.optin .submit{height:42px;margin-top:4px;background:linear-gradient(180deg,var(--gold-light),var(--gold));color:var(--white);font-size:18px;text-align:center;line-height:42px}

/* Features */
.feature{position:absolute;top:582px;width:330px;text-align:center}
.feature-icon{width:86px;height:86px;margin:8px auto 0;background:var(--slate);border:5px solid #e1e2ec;outline:3px solid var(--slate);transform:rotate(45deg)}
.feature h3{margin-top:30px;font-family:"Montserrat",sans-serif;font-weight:400;font-size:20px;color:#333}
.feature p{margin:4px auto 0;width:270px;font-size:13px;line-height:20px;color:var(--muted)}
.btn-outline{display:inline-block;margin-top:12px;width:112px;height:35px;border:2px solid var(--slate);border-radius:18px;font-size:13px;color:#555;line-height:31px}

/* About */
.about{position:absolute;left:0;top:873px;width:1200px;height:374px;overflow:hidden}
.about-photo{position:absolute;inset:0;background:linear-gradient(180deg,#7a86b4 0%,#6a78aa 45%,#57679c 70%,#4b5d93 100%)}
.about h2{position:absolute;top:58px;width:100%;text-align:center;font-family:"Montserrat",sans-serif;font-weight:400;font-size:32px;color:var(--white)}
.about p{position:absolute;left:195px;width:810px;text-align:center;font-size:14px;line-height:23px;color:var(--white)}
.btn-light{position:absolute;left:536px;top:274px;width:126px;height:41px;border:2px solid var(--white);border-radius:21px;color:var(--white);font-size:14px;text-align:center;line-height:37px}

/* Blog */
.blogs{position:absolute;left:0;top:1247px;width:1200px;height:463px;background:var(--light)}
.section-title{position:absolute;width:100%;text-align:center;font-family:"Montserrat",sans-serif;font-weight:400;font-size:30px;color:#333}
.blog-card{position:absolute;top:102px;width:302px;height:306px;background:var(--white);box-shadow:0 1px 4px rgba(0,0,0,.15)}
.blog-card .thumb{height:162px}
.blog-card h3{margin:18px 25px 0;font-family:"Montserrat",sans-serif;font-weight:400;font-size:17px;line-height:21px;color:var(--slate-dark)}
.blog-card p{margin:6px 25px 0;font-size:10.5px;line-height:17px;color:var(--muted);max-height:51px;overflow:hidden}
.blog-card .more{position:absolute;left:25px;bottom:20px;font-size:12px;color:#555}

/* Testimonials */
.stories{position:absolute;left:0;top:1710px;width:1200px;height:319px;background:var(--white);border-top:1px solid #e2e2e2}
.quote-mark{position:absolute;top:86px;font-family:Georgia,serif;font-size:80px;line-height:1;color:var(--quote);font-weight:700}
.stories blockquote{position:absolute;left:210px;top:114px;width:782px;text-align:center;font-style:italic;font-size:13px;line-height:25px;color:#666}
.stories cite{position:absolute;top:194px;width:100%;text-align:center;font-style:normal;font-size:13px;color:#333}

/* Footer */
.site-footer{position:absolute;left:0;top:2029px;width:1200px;height:244px;background:var(--footer)}
.footer-col{position:absolute;top:52px}
.footer-col h4{font-family:"Open Sans",Arial,sans-serif;font-weight:400;font-size:17px;color:var(--white);margin-bottom:10px}
.footer-col li{list-style:none;font-size:12px;line-height:24px;color:#e6e6e6}
.footer-divider{position:absolute;top:52px;width:1px;height:180px;background:#4a4a4a}
.footer-col .note{font-size:11px;color:#e6e6e6;margin-bottom:12px}
.footer-col .email{width:208px;height:32px;background:var(--white);font-size:11px;color:#888;padding:9px 12px}
.footer-col .signup{margin-top:10px;width:96px;height:33px;background:var(--slate);color:var(--white);font-size:14px;text-align:center;line-height:33px}
.social{display:flex;gap:14px;margin-top:13px;padding-left:8px}
.social span{width:22px;height:22px;border-radius:50%;background:#2a2a2a;border:1px solid #5a5a5a}
.footer-bar{position:absolute;left:0;top:2273px;width:1200px;height:59px;background:var(--footer-bar);text-align:center;font-size:12px;color:#ccc;line-height:59px}
</style>
</head>
<body>

<header class="site-header">
  <div class="brand"><span class="brand-mark"></span>Bright Fern Studies</div>
  <span class="nav-marker"></span>
  <nav class="main-nav">
    <a class="active" href="#" style="left:491px">Home</a>
    <a href="#" style="left:575px">About</a>
    <a href="#" style="left:661px">Courses</a>
    <a href="#" style="left:762px">Blog</a>
    <a href="#" style="left:835px">Student Areas</a>
    <a href="#" style="left:982px">Contact</a>
  </nav>
</header>

<section class="hero">
  <div class="hero-photo" role="img" aria-label="Woman meditating with hands together on a rocky shore by a calm blue sea"></div>
  <div class="hero-sea" role="img" aria-label="Calm sea"></div>
  <h1 class="hero-title"><span class="line1">Create your Ideal</span><span class="line2">Reiki Business</span></h1>
  <form class="optin">
    <h2>Stay Inspired</h2>
    <div class="field">First Name</div>
    <div class="field">Last Name</div>
    <div class="field">Email address</div>
    <div class="submit">Yes Count Me In</div>
  </form>
  <svg class="hero-wave" viewBox="0 0 1200 70" preserveAspectRatio="none">
    <path d="M0 70 L0 66 C250 60 420 36 650 36 C860 36 1000 52 1200 52 L1200 70 Z" fill="#ffffff"/>
  </svg>
  <div class="slider-dots" style="left:555px;top:425px"><span class="current"></span><span></span><span></span><span></span></div>
</section>

<div class="feature" style="left:120px">
  <div class="feature-icon" role="img" aria-label="Lotus icon"></div>
  <h3>How Reiki Works</h3>
  <p>Reiki has been used for centuries to help individuals with physical and emotional</p>
  <span class="btn-outline">Click here</span>
</div>
<div class="feature" style="left:430px">
  <div class="feature-icon" role="img" aria-label="Candle icon"></div>
  <h3>Our Courses</h3>
  <p>Learn how to use Reiki to help yourself and others.</p>
  <span class="btn-outline">Click here</span>
</div>
<div class="feature" style="left:740px">
  <div class="feature-icon" role="img" aria-label="Healing session icon"></div>
  <h3>Student Areas</h3>
  <p>Class aptent taciti sociosqu ad litora torquent per conubia nostra</p>
  <span class="btn-outline">Click here</span>
</div>

<section class="about">
  <div class="about-photo" role="img" aria-label="Figure with raised arms standing on a beach at dusk, tinted in blue and violet"></div>
  <h2>About Bright Fern Studies</h2>
  <p style="top:125px">Thought to be centuries old and rediscovered in the late 1800's, Reiki (pronounced ray-key) is a healing and enlightenment system. Reiki can be translated into "Universal (Rei) Life Energy (Ki)". As a practitioner of Reiki, you attune your awareness to this energy and utilize it for the physical and emotional healing of self and others.</p>
  <p style="top:208px">Reiki is non-denominational and can be practiced by everyone, regardless of their religious and spiritual beliefs. Reiki can be performed hands-on in person or from a distance.</p>
  <span class="btn-light">Read More</span>
</section>

<section class="blogs">
  <h2 class="section-title" style="top:50px">Our Blogs</h2>
  <article class="blog-card" style="left:134px">
    <div class="thumb" role="img" aria-label="Stacked stones at sunset" style="background:linear-gradient(180deg,#e59a2c,#b8601a 60%,#3b2412)"></div>
    <h3>How to handle Reiki client no-shows</h3>
    <p>How do you deal with patient no-shows? And then when the same patient wants to reschedule</p>
    <span class="more">READ MORE</span>
  </article>
  <article class="blog-card" style="left:449px">
    <div class="thumb" role="img" aria-label="Woman receiving a relaxing face treatment at a spa" style="background:linear-gradient(135deg,#9a6a3c,#d8b89a 50%,#6e8c6a)"></div>
    <h3>Friday FAQ's July 1st</h3>
    <p>I have a question about the part when performing Reiki and the hands are going through those hand positions for 3-5 minutes at a time...within those</p>
    <span class="more">READ MORE</span>
  </article>
  <article class="blog-card" style="left:766px">
    <div class="thumb" role="img" aria-label="Woman stretching on a sunny beach" style="background:linear-gradient(180deg,#eef0b0,#b9d6c4 55%,#6fa8bd)"></div>
    <h3>How to handle Reiki client no-shows</h3>
    <p>How do you deal with patient no-shows? And then when the same patient wants to reschedule</p>
    <span class="more">READ MORE</span>
  </article>
</section>

<section class="stories">
  <h2 class="section-title" style="top:50px">Success Stories</h2>
  <span class="quote-mark" style="left:165px">&ldquo;</span>
  <span class="quote-mark" style="left:1000px">&rdquo;</span>
  <blockquote>I was drawn to this course with the desire to heal family, friends and pets and this course has given me that ability and more. With it, Reiki has healed me on many levels and given me insight into my own spirituality and to what is possible. The continued contact with Mara Ellison on the community group page as well as input and questions and answers from other students</blockquote>
  <cite>By Author Name</cite>
  <div class="slider-dots dots-grey" style="left:569px;top:243px"><span class="current"></span><span></span><span></span><span></span></div>
</section>

<footer class="site-footer">
  <div class="footer-col" style="left:143px">
    <h4>INFORMATION</h4>
    <ul><li>Home</li><li>About Us</li><li>Our Coures</li><li>Admission</li></ul>
  </div>
  <span class="footer-divider" style="left:281px"></span>
  <div class="footer-col" style="left:320px">
    <h4>COURSES</h4>
    <ul><li>Mauris vel lacus</li><li>Aitae felis</li><li>Vestibulum</li><li>volutpat imperdiet</li></ul>
  </div>
  <span class="footer-divider" style="left:449px"></span>
  <div class="footer-col" style="left:488px">
    <h4>RESOURCES</h4>
    <ul><li>Student Stories</li><li>Our Management</li><li>Our Teachers</li><li>Sitemap</li></ul>
  </div>
  <span class="footer-divider" style="left:633px"></span>
  <div class="footer-col" style="left:681px">
    <h4>SUPPORT</h4>
    <ul><li>FAQ</li><li>Term of Use</li><li>Privacy Policy</li><li>Contact</li></ul>
  </div>
  <span class="footer-divider" style="left:822px"></span>
  <div class="footer-col" style="left:863px">
    <h4>JOB ALERT NOW</h4>
    <p class="note">Please Sign up here for updates</p>
    <div class="email">Email address</div>
    <div class="signup">Sign Up</div>
    <div class="social" aria-label="Social links"><span></span><span></span><span></span><span></span></div>
  </div>
</footer>
<div class="footer-bar">© 2016 Company Name &nbsp;All right reserved &nbsp;Term of Use</div>

</body>
</html>
```